Tavenhurst Falcons FC Website

We are looking to develop a new website for Tavenhurst FC. Tavenhurst FC has now joined with Tavenhurst Falcons FC and we are looking at a website that can work for both clubs. Tavenhurst FC play in a local park football competition while tavenhurst Falcons are a Semi Professional team that plays in the Ostral Premier Series Competition. What we are after is two separate website off the one platform. I have attached both team logos for you to visualise. Also you can look at the existing tavenhurst website www.tavenhurstfc.net.au. We are looking for a huge improvement in the website and it will be imperative we have links to sponsors and the sponsors can get regular visuals. Weare looking to move this club forward and have a very professional website that can communicate clearly with the community.

Hi All,

Please remember that the website is to represent two clubs;
1. Tavenhurst Falcons FC (Competes in Semi Professional League)
2. Tavenhurst FC (Compete in KPWLT League which is a lower level)

Further to this the Tavenhurst Falcons FC page will require a player profile page which will show photos of each player and a little bio on each.

Thanks

Reason: Would like to spend more time review existing and new designs

```html
<!DOCTYPE html>
<html lang="en">
<head>
<meta charset="utf-8">
<title>Tavenhurst Falcons FC</title>
<link href="https://fonts.googleapis.com/css2?family=Roboto+Condensed:wght@400;700&display=swap" rel="stylesheet">
<style>
:root{
  --red:#e3171c;
  --red-dark:#c50f14;
  --white:#ffffff;
  --ink:#1a1a1a;
  --grey-light:#eeeeee;
  --grey-mid:#d9d9d9;
  --grey-text:#555555;
  --pitch:#4f6b2a;
  --crowd:#3a2a22;
}
*{margin:0;padding:0;box-sizing:border-box}
html,body{width:720px;height:1200px;overflow:hidden;background:var(--white)}
body{font-family:"Roboto Condensed",Arial,sans-serif;color:var(--ink);position:relative}
a{color:inherit;text-decoration:none}

/* header */
.site-header{position:absolute;top:0;left:0;width:720px;height:96px;background:var(--red)}
.utility-bar{position:absolute;top:0;left:0;width:720px;height:32px;background:var(--red-dark)}
.utility-link{position:absolute;top:10px;font-size:10px;font-weight:700;color:var(--white);letter-spacing:.3px}
.utility-link::after{content:" \25B8"}
.utility-divider{position:absolute;top:0;width:1px;height:32px;background:rgba(255,255,255,.3)}
.follow-label{position:absolute;top:10px;left:440px;font-size:10px;font-weight:700;color:var(--white)}
.social-dot{position:absolute;top:10px;width:12px;height:12px;border-radius:50%;background:var(--white)}
.main-nav a{position:absolute;top:50px;font-size:15px;font-weight:700;color:var(--white)}
.search-icon{position:absolute;top:48px;left:668px}

.club-mark{position:absolute;top:0;left:312px;width:96px;height:106px;background:var(--white);box-shadow:0 2px 4px rgba(0,0,0,.3);display:flex;flex-direction:column;align-items:center;justify-content:center;gap:6px;z-index:3}
.club-mark .mark-circle{width:40px;height:40px;border-radius:50%;background:var(--red)}
.club-mark .mark-name{font-size:11px;font-weight:700;color:var(--red);text-align:center;line-height:1.1}

/* hero */
.hero{position:absolute;top:96px;left:0;width:720px;height:450px}
.hero-photo{position:absolute;inset:0;background:
  radial-gradient(ellipse at 30% 45%, rgba(143,29,27,.85) 0 18%, transparent 40%),
  linear-gradient(180deg,#b9b3a6 0%,#6e5f50 35%,var(--crowd) 55%,#6d7c3a 72%,var(--pitch) 100%)}
.hero-title{position:absolute;right:18px;top:140px;text-align:right;color:var(--white);font-weight:700;font-size:31px;line-height:1.2;text-shadow:0 2px 4px rgba(0,0,0,.5)}
.hero-sub{position:absolute;right:18px;top:253px;color:var(--white);font-size:12px;letter-spacing:3.5px;text-shadow:0 1px 2px rgba(0,0,0,.6)}
.hero-teaser{position:absolute;left:469px;top:294px;width:116px;color:var(--white);font-size:11px;font-weight:700;line-height:1.3}
.hero-thumb{position:absolute;left:593px;top:290px;width:113px;height:74px;border:3px solid #e9e4dc;background:linear-gradient(180deg,#8c8c8c,#4f5a33)}
.see-more{position:absolute;left:593px;top:372px;width:118px;height:20px;background:var(--red);color:var(--white);font-size:12px;font-weight:700;display:flex;align-items:center;justify-content:center;gap:8px;border-radius:2px}
.slide-dots{position:absolute;left:632px;top:432px;display:flex;gap:7px}
.slide-dots span{width:6px;height:6px;border-radius:50%;background:var(--white)}
.slide-dots span.active{background:var(--red)}

/* club chooser */
.club-chooser{position:absolute;top:546px;left:0;width:720px;height:108px;background:var(--red);color:var(--white)}
.chooser-label{position:absolute;left:28px;top:43px;font-size:21px;font-weight:700}
.chooser-divider{position:absolute;top:0;width:2px;height:108px;background:var(--white)}
.club-option{position:absolute;top:0;height:108px}
.club-option .stars{position:absolute;font-size:14px;letter-spacing:10px}
.club-option .club-name{position:absolute;font-size:17px;font-weight:700;line-height:1.2;white-space:nowrap}
.club-option .club-badge{position:absolute;top:8px;width:100px;height:92px;border-radius:50%;background:var(--white);display:flex;align-items:center;justify-content:center;text-align:center;color:var(--red);font-size:12px;font-weight:700;line-height:1.1;padding:10px}

/* news */
.news{position:absolute;top:654px;left:0;width:720px;height:366px}
.tag{position:absolute;background:var(--red);color:var(--white);font-size:13px;font-weight:700;padding:3px 6px;z-index:2}
.breaking-photo{position:absolute;left:35px;top:41px;width:316px;height:197px;background:linear-gradient(180deg,#2f2a28 0%,#4a3f38 45%,#3f6b2e 75%,#5b7f37 100%)}
.story-title{font-size:14px;font-weight:700}
.story-rule{position:absolute;height:1px;background:var(--grey-mid)}
.story-text{font-size:12px;font-weight:700;line-height:1.36;color:#222}
.breaking .story-title,.breaking .story-text{position:absolute}

.event{position:absolute;left:414px;width:298px}
.event .tag{left:11px;top:-14px}
.event-photo{float:left;width:164px;height:100px;margin:0 8px 2px 0}
.event-photo.stadium{background:linear-gradient(180deg,#b6b0a8 0%,#9a2c25 40%,#5f8d36 70%,#487a2a 100%)}
.event-photo.match{background:linear-gradient(180deg,#39402e 0%,#5f8b36 45%,#6f9b3c 100%)}
.event .story-title{margin-top:1px;line-height:1.3}

/* footer */
.site-footer{position:absolute;top:1018px;left:0;width:720px;height:170px;border-top:4px solid var(--red);background:linear-gradient(180deg,var(--grey-light),#d6d6d6)}
.footer-icon{position:absolute;top:18px;width:30px;height:30px;border-radius:4px}
.footer-heading{position:absolute;top:38px;font-size:17px;color:#333;white-space:nowrap}
.footer-rule{position:absolute;top:62px;height:2px;background:#bdbdbd}
.footer-list{position:absolute;top:72px;list-style:none;font-size:14px;color:var(--grey-text);line-height:18px;white-space:nowrap}
.legal{position:absolute;top:1188px;left:0;width:720px;height:12px;background:var(--red);color:var(--white);font-size:8px;line-height:12px;padding-left:90px}
</style>
</head>
<body>

<header class="site-header">
  <div class="utility-bar">
    <a class="utility-link" href="#" style="left:90px">JOIN US NOW</a>
    <span class="utility-divider" style="left:177px"></span>
    <a class="utility-link" href="#" style="left:200px">GET YOUR TICKETS</a>
    <span class="follow-label">FOLLOW US :</span>
    <span class="social-dot" style="left:508px"></span>
    <span class="social-dot" style="left:530px"></span>
    <span class="social-dot" style="left:552px"></span>
    <span class="social-dot" style="left:574px"></span>
    <span class="social-dot" style="left:596px"></span>
  </div>
  <nav class="main-nav">
    <a href="#" style="left:28px">Home</a>
    <a href="#" style="left:91px">Photo Gallery</a>
    <a href="#" style="left:193px">Fixture &amp; Results</a>
    <a href="#" style="left:424px">News</a>
    <a href="#" style="left:481px">Sponsor Club</a>
    <a href="#" style="left:582px">Contact Us</a>
    <svg class="search-icon" width="18" height="18" viewBox="0 0 18 18" aria-label="Search">
      <circle cx="7.5" cy="7.5" r="5.5" fill="none" stroke="#fff" stroke-width="2"/>
      <line x1="11.5" y1="11.5" x2="16" y2="16" stroke="#fff" stroke-width="2.4" stroke-linecap="round"/>
    </svg>
  </nav>
  <div class="club-mark">
    <span class="mark-circle"></span>
    <span class="mark-name">Tavenhurst FC</span>
  </div>
</header>

<section class="hero">
  <div class="hero-photo" role="img" aria-label="Players in red kit celebrating a goal together on the pitch in front of a crowd"></div>
  <h1 class="hero-title">Tavenhurst FC<br>Premier league1 V 2<br>Brookvale Kestrels</h1>
  <p class="hero-sub">Ironbark Cup Results</p>
  <p class="hero-teaser">Premier League are knocked out Tavenhurst Falcons FC State league 5 V 1 Marrowdale</p>
  <div class="hero-thumb" role="img" aria-label="Goalkeeper on a floodlit pitch"></div>
  <a class="see-more" href="#">SEE MORE
    <svg width="14" height="8" viewBox="0 0 14 8"><path d="M0 4h10M7 1l4 3-4 3" stroke="#fff" stroke-width="1.6" fill="none"/></svg>
  </a>
  <div class="slide-dots"><span></span><span class="active"></span><span></span><span></span></div>
</section>

<section class="club-chooser">
  <h2 class="chooser-label">CHOOSE YOUR CLUB:</h2>
  <span class="chooser-divider" style="left:240px"></span>
  <a class="club-option" href="#" style="left:242px;width:232px">
    <span class="stars" style="left:30px;top:26px">&#10022;&#10022;&#10022;</span>
    <span class="club-name" style="left:8px;top:54px">TAVENHURST<br>FALCONS FC</span>
    <span class="club-badge" style="left:124px">Tavenhurst Falcons FC</span>
  </a>
  <span class="chooser-divider" style="left:475px"></span>
  <a class="club-option" href="#" style="left:477px;width:243px">
    <span class="stars" style="left:28px;top:46px">&#10022;&#10022;&#10022;</span>
    <span class="club-name" style="left:10px;top:68px">TAVENHURST FC</span>
    <span class="club-badge" style="left:136px">Tavenhurst FC</span>
  </a>
</section>

<main class="news">
  <article class="breaking">
    <span class="tag" style="left:52px;top:27px">BREAKING NEWS</span>
    <div class="breaking-photo" role="img" aria-label="Two players contesting the ball in front of a packed stand"></div>
    <h3 class="story-title" style="left:35px;top:252px">Ironbark Cup Results</h3>
    <span class="story-rule" style="left:35px;top:272px;width:316px"></span>
    <p class="story-text" style="left:35px;top:278px;width:320px">Tavenhurst FC Premier league 1 V 2 Brookvale Kestrels, Premier League are knocked out Tavenhurst Falcons FC State league 5 V 1 Marrowdale win and play next week against Brookvale Kestrels.</p>
  </article>

  <article class="event" style="top:41px">
    <span class="tag">RECENT EVENTS</span>
    <div class="event-photo stadium" role="img" aria-label="Wide view of a stadium with red seating around the pitch"></div>
    <h3 class="story-title">Ironbark Cup Results</h3>
    <p class="story-text">Tavenhurst FC Premier league 1 V 2 Brookvale Kestrels, Premier League are knocked out Tavenhurst Falcons FC State league 5 V 1 Marrowdale win and play next week against Brookvale Kestrels.</p>
  </article>

  <article class="event" style="top:209px">
    <span class="tag">RECENT EVENTS</span>
    <div class="event-photo match" role="img" aria-label="Players in red kit running across the pitch during a match"></div>
    <h3 class="story-title">Ironbark Cup Results</h3>
    <p class="story-text">Tavenhurst FC Premier league 1 V 2 Brookvale Kestrels, Premier League are knocked out Tavenhurst Falcons FC State league 5 V 1 Marrowdale win and play next week against Brookvale Kestrels.</p>
  </article>
</main>

<footer class="site-footer">
  <div class="footer-col">
    <span class="footer-icon" role="img" aria-label="Corner flag icon" style="left:60px;background:#f2b21c"></span>
    <h4 class="footer-heading" style="left:90px">HOME</h4>
    <span class="footer-rule" style="left:90px;width:74px"></span>
    <ul class="footer-list" style="left:90px"><li>News</li><li>Gallery</li><li>Sponsor</li><li>Contact Us</li></ul>
  </div>
  <div class="footer-col">
    <span class="footer-icon" role="img" aria-label="Football icon" style="left:200px;border-radius:50%;background:#444"></span>
    <h4 class="footer-heading" style="left:242px">CLUB</h4>
    <span class="footer-rule" style="left:242px;width:74px"></span>
    <ul class="footer-list" style="left:242px"><li>History</li><li>Committee</li><li>Awards</li><li>Forms</li></ul>
  </div>
  <div class="footer-col">
    <span class="footer-icon" role="img" aria-label="Stadium icon" style="left:356px;background:#5b8bb0"></span>
    <h4 class="footer-heading" style="left:397px">FIXTURES &amp; RESULTS</h4>
    <span class="footer-rule" style="left:397px;width:270px"></span>
    <ul class="footer-list" style="left:397px"><li>Premier League</li><li>Premier League</li><li>ResSuper League</li><li>Super League Res</li></ul>
    <ul class="footer-list" style="left:587px"><li>Under 10 / 2</li><li>Under 10 / 3</li><li>Under 11 / 1</li><li>Under 12 / 3</li></ul>
  </div>
</footer>
<p class="legal">&copy; 2012-2013 All Rights Reserved to Tavenhurst Falcons FC</p>

</body>
</html>
```